Redesign of business card for Cedar Ridge Mechanical

We are looking for a new design for our business cards for Cedar Ridge Mechanical. We are a plumbing & HVAC construction company, operating on the West Coast of Canada and USA. Logo attached.
Industry/Entity Type
Construction - Plumbing & HVAC
Contact Information for Business Card
Name, address, phone numbers, email, website address
Look and feel
Each slider illustrates characteristics of the customer's brand and the style your logo design should communicate.

```html
<!DOCTYPE html>
<html lang="en">
<head>
<meta charset="utf-8">
<title>Cedar Ridge Mechanical – Business Card</title>
<link href="https://fonts.googleapis.com/css2?family=Poppins:wght@300;400;700&family=Oswald:wght@600&display=swap" rel="stylesheet">
<style>
  :root {
    --bg: #232323;
    --card-light: #e3e4e3;
    --card-dark: #121214;
    --ink: #0d0d0d;
    --emboss: #1e1e22;
    --white: #ffffff;
    --rule: #3a3a3a;
  }
  * { margin: 0; padding: 0; box-sizing: border-box; }
  html, body { width: 1200px; height: 780px; overflow: hidden; background: var(--bg); }
  .canvas {
    width: 1200px; height: 780px;
    display: flex; align-items: center; justify-content: center; gap: 50px;
    font-family: "Poppins", sans-serif;
  }
  .card { width: 525px; height: 300px; position: relative; overflow: hidden; }

  /* Front */
  .card--front { background: var(--card-light); color: var(--ink); }
  .brand-block {
    position: absolute; left: 34px; top: 58px; width: 200px;
    display: flex; align-items: center; gap: 12px;
  }
  .brand-square { width: 30px; height: 30px; background: var(--ink); flex: none; }
  .brand-name {
    font-family: "Poppins", sans-serif; font-weight: 700; font-size: 21px;
    line-height: 1.1; text-transform: uppercase; color: var(--ink);
  }
  .divider {
    position: absolute; left: 262px; top: 34px; width: 1px; height: 190px;
    background: var(--rule);
  }
  .contact-block { position: absolute; left: 290px; top: 60px; }
  .person-name { font-size: 27px; line-height: 1.1; }
  .person-name .first { font-weight: 700; }
  .person-name .last { font-weight: 300; }
  .person-title { font-size: 13px; font-weight: 400; margin-top: 2px; }
  .contact-list { list-style: none; margin-top: 16px; font-size: 13px; font-weight: 400; }
  .contact-list li { display: flex; align-items: center; gap: 9px; line-height: 1.55; }
  .contact-list svg { width: 12px; height: 12px; flex: none; }

  .address-band {
    position: absolute; left: 0; bottom: 0; width: 100%; height: 40px;
    background: var(--ink); color: var(--white);
    display: flex; align-items: center; padding-left: 24px;
    font-size: 13px; font-weight: 400;
  }
  .band-mark {
    position: absolute; right: 22px; bottom: 0; height: 58px; width: 150px;
    background: var(--card-light); border: 3px solid var(--ink); border-bottom: none;
    display: flex; align-items: center; justify-content: center; gap: 7px;
    border-radius: 6px 6px 0 0;
  }
  .band-mark .brand-square { width: 12px; height: 12px; }
  .band-mark .brand-name { font-size: 11px; }

  /* Back */
  .card--back {
    background: var(--card-dark);
    display: flex; align-items: center; justify-content: center; gap: 18px;
  }
  .card--back .brand-square { width: 46px; height: 46px; background: var(--emboss); }
  .card--back .brand-name { font-size: 30px; color: var(--emboss); width: 260px; }
</style>
</head>
<body>
<main class="canvas">
  <section class="card card--front" aria-label="Business card front">
    <div class="brand-block">
      <span class="brand-square"></span>
      <span class="brand-name">Cedar Ridge Mechanical</span>
    </div>
    <div class="divider"></div>
    <div class="contact-block">
      <h1 class="person-name"><span class="first">Marta</span> <span class="last">Kovanda</span></h1>
      <p class="person-title">Founder &amp; CEO</p>
      <ul class="contact-list">
        <li>
          <svg viewBox="0 0 24 24" aria-hidden="true"><path fill="currentColor" d="M6.6 10.8a15.1 15.1 0 0 0 6.6 6.6l2.2-2.2a1 1 0 0 1 1-.25 11.4 11.4 0 0 0 3.6.57 1 1 0 0 1 1 1V20a1 1 0 0 1-1 1A17 17 0 0 1 3 4a1 1 0 0 1 1-1h3.5a1 1 0 0 1 1 1c0 1.25.2 2.45.57 3.57a1 1 0 0 1-.25 1z"/></svg>
          (555) 214-3067
        </li>
        <li>
          <svg viewBox="0 0 24 24" aria-hidden="true"><rect x="2" y="5" width="20" height="14" rx="1.5" fill="none" stroke="currentColor" stroke-width="2"/><path d="M3 6l9 7 9-7" fill="none" stroke="currentColor" stroke-width="2"/></svg>
          info@cedarridgemech.com
        </li>
        <li>
          <svg viewBox="0 0 24 24" aria-hidden="true"><circle cx="12" cy="12" r="9.5" fill="none" stroke="currentColor" stroke-width="2"/><path d="M2.5 12h19M12 2.5c3 3 3 16 0 19M12 2.5c-3 3-3 16 0 19" fill="none" stroke="currentColor" stroke-width="1.6"/></svg>
          www.cedarridgemech.com
        </li>
      </ul>
    </div>
    <div class="address-band">1840 Harbor Ln. Suite 310 Tacoma, WA 98402</div>
    <div class="band-mark">
      <span class="brand-square"></span>
      <span class="brand-name">Cedar Ridge</span>
    </div>
  </section>

  <section class="card card--back" aria-label="Business card back">
    <span class="brand-square"></span>
    <span class="brand-name">Cedar Ridge Mechanical</span>
  </section>
</main>
</body>
</html>
```